Tidal Forge - Crypto Currency Miner Powered by Renewable Energy Website

We Need Web Pages Design for Website for Crypto Currency Miner

Serivices include:
Mining Rig Sales
Housing for Rigs turnkey on renewable energy grid
Cloud Mining term packages
Updates

http://www.vaultrigsurvey.example (Competitors sites)

Target Market(s)

Investers for Mining Rigs and terms for 1,2 or 3 years of Hash rate

Industry/Entity Type

Mining

Number of Pages Required

5+ page

Font styles to use
Sans Serif

Colors
add136
9bcb3c
606060
474747
ffc214
cadf82
fbee3e
876aae
6b449b

Requirements
Must have
• Pictures of Solar, Wind and power Factor Correction units
Nice to have
• e-commerce platform so contract terms can be purchased through website
Should not have
• Heavy construction equipment

```html
<!DOCTYPE html>
<html lang="en">
<head>
<meta charset="utf-8">
<title>Tidal Forge – Crypto Currency Miner</title>
<link rel="stylesheet" href="https://fonts.googleapis.com/css2?family=Open+Sans:wght@400;600;700&family=Oswald:wght@400;500&display=swap">
<style>
:root{
  --green:#5aa42a;
  --green-dark:#2f8a22;
  --green-light:#9bcb3c;
  --text:#474747;
  --text-soft:#606060;
  --yellow:#ffc214;
  --red:#d8112b;
  --dark:#2b2f33;
  --white:#ffffff;
  --line:#e2e2e2;
}
*{box-sizing:border-box;margin:0;padding:0}
html,body{width:1200px;height:2866px;overflow:hidden}
body{font-family:"Open Sans",Arial,sans-serif;color:var(--text);background:var(--white);position:relative}
.abs{position:absolute}

/* header */
.topbar{left:360px;top:0;width:840px;height:40px;background:var(--green);clip-path:polygon(0 0,100% 0,100% 100%,40px 100%)}
.topbar .contact{position:absolute;left:70px;top:10px;color:#fff;font-size:14px;display:flex;gap:12px;align-items:center}
.topbar .social{position:absolute;right:36px;top:11px;display:flex;gap:9px}
.topbar .social span{width:17px;height:17px;background:#fff;border-radius:3px;display:block}
.brand{left:96px;top:34px;display:flex;align-items:center;gap:10px}
.brand .mark{width:46px;height:46px;border-radius:50%;background:var(--green-dark)}
.brand .name{font-size:30px;font-weight:700;color:var(--green-dark);letter-spacing:-.5px}
.nav{top:76px;left:386px;display:flex;gap:0}
.nav a{font-size:17px;color:var(--text);text-decoration:none;width:135px;text-align:center}
.nav a.active{color:var(--green)}

/* hero */
.hero{left:0;top:130px;width:1200px;height:488px;background:linear-gradient(180deg,#6f79c4 0%,#a99bd0 38%,#7c8fb0 55%,#4f7a3a 72%,#2f5b22 100%)}
.hero h1{position:absolute;right:210px;top:155px;font-family:"Oswald",Arial,sans-serif;font-weight:500;color:#fff;font-size:78px;line-height:1;text-align:center}
.hero h1 small{display:block;font-size:52px;font-weight:400;margin-top:10px}
.hero .arrows{position:absolute;right:42px;bottom:48px;display:flex;gap:8px}
.hero .arrows span{width:18px;height:18px;background:rgba(0,0,0,.45);border-radius:2px;display:flex;align-items:center;justify-content:center}

/* welcome */
.welcome-title{top:712px;left:0;width:1200px;text-align:center;font-size:32px;font-weight:600;color:#222}
.welcome-text{top:766px;left:180px;width:840px;text-align:center;font-size:14.5px;line-height:26px;color:var(--text)}
.feature{top:893px;width:300px;text-align:center}
.feature .ring{width:118px;height:118px;margin:0 auto;border-radius:50%;border:3px solid var(--green-dark);padding:5px}
.feature .ring div{width:100%;height:100%;border-radius:50%;background:linear-gradient(180deg,#4fae3a,#1f7d22);display:flex;align-items:center;justify-content:center}
.feature h3{margin-top:18px;font-size:20px;font-weight:400;line-height:27px;color:#222}
.feature p{margin-top:16px;font-size:14px;line-height:22px;color:var(--text-soft)}

/* what we do */
.wwd-photo{left:560px;top:1247px;width:640px;height:410px;background:radial-gradient(circle at 55% 60%,#c7a46a 0%,#6a5a45 22%,#1c2233 55%,#0b0d18 100%)}
.wwd-panel{left:0;top:1247px;width:780px;height:410px;background:linear-gradient(135deg,#6aa829,#4f9a25 60%,#3f8a22);clip-path:polygon(0 0,100% 0,624px 100%,0 100%)}
.wwd-panel h2{position:absolute;left:97px;top:60px;font-size:33px;font-weight:600;color:#fff}
.wwd-panel p{position:absolute;left:90px;top:112px;width:518px;font-size:14.5px;line-height:27.5px;color:#fff;text-align:justify}
.btn-outline{position:absolute;left:90px;top:320px;border:1px solid #fff;color:#fff;font-size:14px;padding:6px 14px;border-radius:3px}

/* blog */
.blog-title{top:1765px;left:0;width:1200px;text-align:center;font-size:32px;font-weight:500;color:#111}
.post{top:1842px;width:312px}
.post .thumb{height:174px;position:relative}
.post .meta{position:absolute;left:0;bottom:0;display:flex;font-size:12px;color:#fff}
.post .meta .date{background:var(--red);padding:3px 14px}
.post .meta .comments{background:#1b1b1b;padding:3px 10px}
.post h4{margin-top:22px;font-size:17px;font-weight:400;color:#222}
.post p{margin-top:10px;font-size:14px;line-height:24px;color:var(--text-soft)}
.post a{display:block;margin-top:6px;font-size:14px;color:var(--green-dark);text-decoration:none}

/* cta band */
.cta{left:0;top:2207px;width:1200px;height:325px;background:linear-gradient(180deg,#2c3034,#3a3f44 60%,#2a2d31);text-align:center;color:#fff}
.cta h2{margin-top:64px;font-size:32px;font-weight:600;letter-spacing:.5px}
.cta h3{margin-top:14px;font-size:21px;font-weight:600}
.cta p{margin:14px auto 0;width:900px;font-size:15.5px;line-height:25px}
.cta .btn{display:inline-block;margin-top:22px;background:var(--yellow);color:#fff;font-size:15px;padding:10px 30px;border-radius:24px}

/* footer */
.foot-brand{left:112px;top:2622px;display:flex;align-items:center;gap:8px}
.foot-brand .mark{width:36px;height:36px;border-radius:50%;background:var(--green-dark)}
.foot-brand .name{font-size:23px;font-weight:700;color:var(--green-dark)}
.foot-social{left:126px;top:2712px;display:flex;gap:10px}
.foot-social span{width:30px;height:30px;border-radius:50%;display:block}
.foot-col{top:2598px}
.foot-col h5{font-size:17px;font-weight:600;color:#222;letter-spacing:.5px;margin-bottom:18px}
.foot-col li{list-style:none;font-size:13.5px;color:var(--text);height:27px;display:flex;align-items:center;gap:8px}
.foot-col li::before{content:"»";font-weight:700}
.foot-col.contact li::before{content:none}
.foot-col.contact li{align-items:flex-start;height:auto;margin-bottom:14px;line-height:22px}
.foot-col.contact svg{flex:none;margin-top:4px}
.divider{left:82px;top:2800px;width:1030px;height:1px;background:var(--line)}
.copyright{left:0;top:2829px;width:1200px;text-align:center;font-size:12.5px;color:var(--text)}
</style>
</head>
<body>

<header>
  <div class="abs topbar">
    <div class="contact">
      <svg width="12" height="12" viewBox="0 0 24 24"><path fill="#fff" d="M6.6 10.8a15 15 0 006.6 6.6l2.2-2.2a1 1 0 011-.25 11.4 11.4 0 003.6.6 1 1 0 011 1V20a1 1 0 01-1 1A17 17 0 013 4a1 1 0 011-1h3.5a1 1 0 011 1c0 1.25.2 2.45.6 3.6a1 1 0 01-.25 1z"/></svg>
      <span>1.555.301.2290</span><span>|</span>
      <svg width="14" height="11" viewBox="0 0 24 18"><rect width="24" height="18" rx="2" fill="#fff"/><path d="M1 1l11 9 11-9" stroke="#5aa42a" stroke-width="2" fill="none"/></svg>
      <span>hello@tidalforge.example</span>
    </div>
    <div class="social"><span></span><span></span><span></span><span></span></div>
  </div>
  <div class="abs brand"><span class="mark"></span><span class="name">Tidal Forge</span></div>
  <nav class="abs nav">
    <a class="active">Home</a><a>About us</a><a>Our Offer</a><a>Services</a><a>Blog</a><a>Contact us</a>
  </nav>
</header>

<section class="abs hero" role="img" aria-label="Wind turbines on green hills under a purple evening sky">
  <h1>TIDAL FORGE<small>Crypto Currency Miner</small></h1>
  <div class="arrows">
    <span><svg width="8" height="10" viewBox="0 0 8 10"><path d="M6 1L2 5l4 4" stroke="#fff" stroke-width="2" fill="none"/></svg></span>
    <span><svg width="8" height="10" viewBox="0 0 8 10"><path d="M2 1l4 4-4 4" stroke="#fff" stroke-width="2" fill="none"/></svg></span>
  </div>
</section>

<section>
  <h2 class="abs welcome-title">WELCOME TO THE TIDAL FORGE</h2>
  <p class="abs welcome-text">It is a long established fact that a reader will be distracted by the readable content of a page when looking at its layout. The point of using Lorem Ipsum is that it has a more-or-less normal distribution of letters, as opposed &nbsp;to using 'Content here, content here', making it look like readable English Many desktop publishing packages</p>

  <div class="abs feature" style="left:113px">
    <div class="ring"><div>
      <svg width="46" height="52" viewBox="0 0 46 52" fill="#fff"><rect x="6" y="2" width="34" height="11" rx="1"/><rect x="6" y="16" width="34" height="11" rx="1"/><rect x="6" y="30" width="34" height="11" rx="1"/><rect x="21" y="41" width="4" height="6"/><rect x="4" y="47" width="38" height="3"/></svg>
    </div></div>
    <h3>Your hardware<br>is already running</h3>
    <p>The point of using Lorem Ipsum is<br>that it has a more-or-less normal</p>
  </div>
  <div class="abs feature" style="left:447px">
    <div class="ring"><div>
      <svg width="50" height="50" viewBox="0 0 50 50" fill="#fff"><ellipse cx="25" cy="10" rx="18" ry="6"/><rect x="7" y="14" width="36" height="7" rx="3"/><rect x="7" y="23" width="36" height="7" rx="3"/><rect x="7" y="32" width="36" height="7" rx="3"/><rect x="7" y="41" width="36" height="7" rx="3"/></svg>
    </div></div>
    <h3>Mine alternative<br>cryptocurrencies</h3>
    <p>The point of using Lorem Ipsum is<br>that it has a more-or-less normal</p>
  </div>
  <div class="abs feature" style="left:775px">
    <div class="ring"><div>
      <svg width="46" height="40" viewBox="0 0 46 40"><rect x="2" y="6" width="42" height="32" rx="4" fill="#fff"/><rect x="28" y="16" width="16" height="12" rx="2" fill="#2a8a25"/><circle cx="34" cy="22" r="2" fill="#fff"/><path d="M6 6l24-5 3 5" fill="#fff"/></svg>
    </div></div>
    <h3>Get your first<br>payout today</h3>
    <p>The point of using Lorem Ipsum is<br>that it has a more-or-less normal</p>
  </div>
</section>

<section>
  <div class="abs wwd-photo" role="img" aria-label="Close-up of gold crypto coins lit in blue and amber"></div>
  <div class="abs wwd-panel">
    <h2>What We do</h2>
    <p>It is a long established fact that a reader will be distracted by the readable content of a page when looking at its layout. The point of using Lorem Ipsum is that it has a more-or-less normal distribution of letters, as opposed to using 'Content here, content here', making it look like readable English. Many desktop publishing packages and web page editors now use Lorem Ipsum as their default model text, and a search for 'lorem ipsum' will uncover many web sites still in their infancy.</p>
    <span class="btn-outline">Read More »</span>
  </div>
</section>

<section>
  <h2 class="abs blog-title">Latest Blog</h2>
  <article class="abs post" style="left:93px">
    <div class="thumb" role="img" aria-label="Solar panels and wind turbines in a green field" style="background:linear-gradient(180deg,#3c86d6 0%,#8fc0ea 45%,#2c4f7a 60%,#4f8a30 100%)">
      <div class="meta"><span class="date">Dec 03</span><span class="comments">0</span></div>
    </div>
    <h4>Neque porro quisquam est qui</h4>
    <p>It has survived not only five centuries, but also the leap into electronic typesetting,</p>
    <a>Read More »</a>
  </article>
  <article class="abs post" style="left:441px">
    <div class="thumb" role="img" aria-label="House roof with solar panels and turbines under bright sun" style="background:linear-gradient(160deg,#e8f2fb 0%,#4f95d6 35%,#a4512f 65%,#5f3a28 100%)">
      <div class="meta"><span class="date">Dec 03</span><span class="comments">0</span></div>
    </div>
    <h4>Dolorem ipsum quia dolor sit amet</h4>
    <p>It has survived not only five centuries, but also the leap into electronic typesetting,</p>
    <a>Read More »</a>
  </article>
  <article class="abs post" style="left:795px">
    <div class="thumb" role="img" aria-label="Rows of solar panels at sunset" style="background:linear-gradient(180deg,#5f86b4 0%,#e9d6a8 40%,#2a3a55 62%,#4d7a2a 100%)">
      <div class="meta"><span class="date">Dec 03</span><span class="comments">0</span></div>
    </div>
    <h4>Quisquam est qui dolorem ipsum quia</h4>
    <p>It has survived not only five centuries, but also the leap into electronic typesetting,</p>
    <a>Read More »</a>
  </article>
</section>

<section class="abs cta" role="img" aria-label="Dark view of a wind and solar farm">
  <h2>CRYPTO CURRENCY MINER</h2>
  <h3>NEQUE PORRO QUISQUAM EST QUI DOLOREM IPSUM QUIA</h3>
  <p>It is a long established fact that a reader will be distracted by the readable content of a page when looking at its layout. The point of using Lorem Ipsum is that it has a more-or-less normal distribution of letters, as opposed to using</p>
  <span class="btn">VIEW MORE »</span>
</section>

<footer>
  <div class="abs foot-brand"><span class="mark"></span><span class="name">Tidal Forge</span></div>
  <div class="abs foot-social">
    <span style="background:#2d4f9a"></span><span style="background:#d8392b"></span><span style="background:#39a6e8"></span>
  </div>
  <div class="abs foot-col" style="left:408px">
    <h5>QUICK LINKS</h5>
    <ul><li>Privacy Policy</li><li>Login</li><li>Advanced Search</li><li>Contact Us</li></ul>
  </div>
  <div class="abs foot-col" style="left:680px">
    <h5>LINKS</h5>
    <ul><li>About</li><li>Services</li><li>Blog</li><li>Content</li></ul>
  </div>
  <div class="abs foot-col contact" style="left:908px">
    <h5>CONTACT US</h5>
    <ul>
      <li><svg width="14" height="16" viewBox="0 0 14 18"><path fill="#2f8a22" d="M7 0a7 7 0 00-7 7c0 5 7 11 7 11s7-6 7-11a7 7 0 00-7-7zm0 10a3 3 0 110-6 3 3 0 010 6z"/></svg><span>P.O. Box 1180 Lakeview,<br>OR 97630</span></li>
      <li><svg width="14" height="14" viewBox="0 0 24 24"><path fill="#2f8a22" d="M6.6 10.8a15 15 0 006.6 6.6l2.2-2.2a1 1 0 011-.25 11.4 11.4 0 003.6.6 1 1 0 011 1V20a1 1 0 01-1 1A17 17 0 013 4a1 1 0 011-1h3.5a1 1 0 011 1c0 1.25.2 2.45.6 3.6a1 1 0 01-.25 1z"/></svg><span>555.718.4402</span></li>
      <li><svg width="15" height="12" viewBox="0 0 24 18"><rect width="24" height="18" rx="2" fill="#2f8a22"/><path d="M1 1l11 9 11-9" stroke="#fff" stroke-width="2" fill="none"/></svg><span>hello@tidalforge.example</span></li>
    </ul>
  </div>
  <div class="abs divider"></div>
  <p class="abs copyright">Copyright © 2018 &nbsp;All Rights Reserved</p>
</footer>

</body>
</html>
```